Meadow Paw Web Site

We have basically a start up business that I need help with. This project is just for the web site.

Our product is a frozen raw pet food that promotes weight control, less shedding, smaller stools and an overall better health. The product is in nugget form similar to what you would see in a steak shish kabob. I only share that with you in case you want to incorporate that in the design.

We have been in business for 17 years but all of our sales have been word of mouth. We are going to be launching an infomercial this summer and I need everything stated previously to be completed before we can launch the infomercial.

We need the following (6) pages:

Home:
This is where we need to have the ability to purchase our products. Our main goal is to get the consumer to purchase our product. We have our own shopping cart so we just need to allow for the insertion of that shopping cart.

Why Raw:
This will just be a page with 4-5 paragraphs and an embedded YouTube video.

How to Use:
We will need a page with a chart (4 Columns wide with 6 rows) as well as an embedded YouTube video.

Customer Success Stories:
Allow us to add these as we move forward. I need a placeholder for an image of the customers pet and a paragraph or two explaining the situation

Where to Buy:
- Online - Find a Retailer - Find a Local Distributor - Call to Order

Contact Us:
Copper Ridge Holdings, Inc.
2740 Copper Rd
Eagan, MN 55148
(800) xxx-xxxx

We need to provide links to our to be created... Facebook page, Twitter Account, Youtube Channel, Google circle, Blog
Updates

All, I have received many front page designs that look good.  Please notice in the brief that I need multiple pages built not just the home page.  

Thanks,

Dale

Reason: I need to see the rest of the pages. Thanks, Dale

Target Market(s)

Women between the ages of 30 & 60.

Industry/Entity Type

Shopping

```html
<!DOCTYPE html>
<html lang="en">
<head>
<meta charset="utf-8">
<title>Meadow Paw – Home</title>
<link rel="stylesheet" href="https://fonts.googleapis.com/css2?family=Open+Sans:wght@400;600;700&display=swap">
<style>
:root{
  --orange:#e8731a;
  --orange-dark:#c65a0c;
  --orange-light:#f39a3c;
  --yellow:#f6c51d;
  --ink:#333;
  --muted:#777;
  --panel:#ffffff;
  --footer:#2b2b2b;
  --footer-bar:#1e1e1e;
  --footer-text:#a9a9a9;
}
*{box-sizing:border-box;margin:0;padding:0}
html,body{width:670px;height:1200px;overflow:hidden}
body{font-family:"Open Sans",Arial,sans-serif;color:var(--ink);
  background:linear-gradient(90deg,#cfcfcf 0,#ececec 12%,#f3f3f3 50%,#ececec 88%,#cfcfcf 100%);position:relative}
.wrap{position:absolute;left:67px;width:536px}

/* header */
.utility{top:8px;text-align:right;font-size:6.5px;color:var(--muted);letter-spacing:.3px;white-space:nowrap}
.utility span{margin-left:6px}
.brand{position:absolute;left:67px;top:16px;display:flex;align-items:center;gap:7px;font-weight:700;font-size:19px;color:var(--orange-dark);white-space:nowrap}
.brand i{width:16px;height:16px;background:var(--orange);display:block}
.tagline{position:absolute;left:67px;top:44px;font-size:6px;color:var(--muted);letter-spacing:.4px;white-space:nowrap}
.account{position:absolute;right:67px;top:36px;display:flex;gap:5px}
.btn{font-size:7px;font-weight:700;padding:3px 9px;border-radius:3px;color:#fff;background:var(--orange);white-space:nowrap}
.btn.alt{background:var(--yellow);color:#5a3a00}
.cart{position:absolute;left:330px;top:64px;font-size:7px;color:var(--ink);display:flex;align-items:center;gap:4px;white-space:nowrap}
.cart b{color:var(--orange)}
.search{position:absolute;right:67px;top:60px;width:130px;height:17px;border:1px solid #ccc;border-radius:9px;background:#fff;font-size:7px;color:#999;padding:3px 8px}
.search svg{position:absolute;right:6px;top:3px}
.nav{top:94px;height:28px;border-radius:3px;background:linear-gradient(var(--orange-light),var(--orange-dark));display:flex;align-items:center;padding-left:10px}
.nav a{color:#fff;font-size:8.5px;font-weight:700;text-decoration:none;padding:0 16px;border-right:1px solid rgba(255,255,255,.35);line-height:28px;height:28px;white-space:nowrap}
.nav a:last-child{border-right:0}
.nav .home{display:flex;align-items:center;gap:4px}

/* hero */
.hero-main{position:absolute;left:67px;top:134px;width:378px;height:190px;border-radius:8px;overflow:hidden;
  background:linear-gradient(160deg,#8fb86a,#c99a55 55%,#e6c27a)}
.hero-caption{position:absolute;left:0;right:0;bottom:0;padding:8px 14px;background:rgba(0,0,0,.28);color:#fff;font-size:13px;font-weight:600;text-align:center;line-height:1.2}
.hero-side{position:absolute;left:455px;top:134px;width:148px;height:190px;border-radius:8px;overflow:hidden;background:#5a8a3c}
.hero-side .photo{height:150px;background:linear-gradient(170deg,#9cc07a,#b58a50 70%)}
.hero-side .cta{height:40px;background:var(--orange);color:#fff;font-size:14px;font-weight:700;text-align:center;line-height:40px;letter-spacing:.5px;white-space:nowrap}
.dots{position:absolute;left:292px;top:330px;display:flex;gap:5px}
.dots i{width:7px;height:7px;border-radius:50%;background:#bbb;display:block}
.dots i.on{background:#888}

/* videos */
.section-tab{position:absolute;left:67px;top:356px;width:536px;height:22px;border-bottom:2px solid var(--orange)}
.section-tab span{display:inline-block;height:20px;line-height:20px;padding:0 10px;background:linear-gradient(var(--orange-light),var(--orange-dark));color:#fff;font-size:9px;font-weight:700;border-radius:3px 3px 0 0}
.videos{top:380px;height:636px;background:var(--panel);padding:8px 0}
.video{display:flex;height:155px;padding:6px 0}
.thumb{width:178px;height:140px;border-radius:4px;position:relative;flex:none}
.thumb svg{position:absolute;left:71px;top:52px}
.t1{background:linear-gradient(160deg,#f0ede6,#c9b38e)}
.t2{background:linear-gradient(160deg,#8db36b,#5f8d3f)}
.t3{background:linear-gradient(170deg,#9fc67b,#4d7f2d)}
.t4{background:linear-gradient(160deg,#b8aea3,#6c6a66)}
.copy{padding:4px 0 0 16px}
.copy h2{font-size:12.5px;color:var(--orange);font-weight:700;margin-bottom:5px;white-space:nowrap}
.copy p{font-size:7.4px;line-height:11px;color:#555}

/* footer */
.footer{position:absolute;left:0;top:1027px;width:670px;height:173px;background:var(--footer)}
.cols{position:absolute;left:67px;top:14px;width:536px;display:flex}
.col h3{color:#fff;font-size:9px;font-weight:700;margin-bottom:6px;white-space:nowrap}
.col li{list-style:none;font-size:6.8px;color:var(--footer-text);line-height:10.5px;white-space:nowrap}
.c1{width:85px}.c2{width:89px}.c3{width:101px}.c4{width:127px}.c5{width:134px}
.c4 li{display:flex;align-items:center;gap:4px}
.c5 p{font-size:6.8px;color:var(--footer-text);line-height:9.5px;margin-bottom:6px}
.field{height:13px;background:#fff;border-radius:2px;margin-bottom:5px}
.subscribe{display:inline-block;background:var(--orange);color:#fff;font-size:7px;font-weight:700;padding:3px 9px;border-radius:2px;margin-left:60px}
.social{display:flex;gap:4px;margin-top:6px;justify-content:flex-end}
.social i{width:12px;height:12px;display:block;background:#555;border-radius:2px}
.social i:nth-child(2){background:#777}
.social i:nth-child(4){background:var(--orange)}
.bottom{position:absolute;left:0;bottom:0;width:670px;height:22px;background:var(--footer-bar);font-size:6.5px;color:#888;line-height:22px;padding-left:67px}
</style>
</head>
<body>

<div class="wrap utility"><span>MY ACCOUNT</span> | <span>WISH LIST</span> | <span>MY CART</span> | <span>CHECKOUT</span></div>
<div class="brand"><i></i>Meadow Paw</div>
<div class="tagline">FROZEN RAW NUGGETS · BETTER HEALTH</div>
<div class="account"><span class="btn">Sign in</span><span class="btn alt">Register</span></div>
<div class="cart">
  <svg width="12" height="10" viewBox="0 0 12 10"><path d="M0 1h2l2 6h6l1.5-4.5H3" fill="none" stroke="#e8731a" stroke-width="1.2"/><circle cx="5" cy="9" r="1" fill="#e8731a"/><circle cx="9" cy="9" r="1" fill="#e8731a"/></svg>
  SHOPPING CART <b>(0) ITEMS</b>
</div>
<div class="search">Search...
  <svg width="10" height="10" viewBox="0 0 10 10"><circle cx="4" cy="4" r="3" fill="none" stroke="#e8731a" stroke-width="1.3"/><path d="M6.3 6.3 9 9" stroke="#e8731a" stroke-width="1.5"/></svg>
</div>

<nav class="wrap nav">
  <a class="home" href="#"><svg width="9" height="8" viewBox="0 0 9 8"><path d="M4.5 0 0 4h1.2v4h2.3V5.5h2V8h2.3V4H9z" fill="#fff"/></svg>Home</a>
  <a href="#">Why Raw</a><a href="#">How to Use</a><a href="#">Where to Buy</a><a href="#">Success Stories</a><a href="#">Contact Us</a>
</nav>

<div class="hero-main" role="img" aria-label="Three puppies lying side by side on a lawn">
  <div class="hero-caption">There are many variations of<br>passages of Lorem</div>
</div>
<div class="hero-side">
  <div class="photo" role="img" aria-label="Puppy standing in the grass"></div>
  <div class="cta">CALL TO ORDER</div>
</div>
<div class="dots"><i class="on"></i><i></i><i></i><i></i></div>

<div class="section-tab"><span>Our Video</span></div>
<section class="wrap videos">
  <article class="video">
    <div class="thumb t1" role="img" aria-label="Video still of a bulldog and a puppy playing">
      <svg width="36" height="36" viewBox="0 0 36 36"><circle cx="18" cy="18" r="17" fill="rgba(0,0,0,.55)" stroke="#fff" stroke-width="2"/><path d="M14 11v14l11-7z" fill="#fff"/></svg>
    </div>
    <div class="copy">
      <h2>Nulla ullamcorper lacus eget purus</h2>
      <p>Praesent lacinia ullamcorper dolor, eget tempor est facilisis ut. Nullam pretium, nulla et vehicula dapibus, erat leo tincidunt tortor, vitae viverra odio lectus sed metus. Curabitur at magna eget lorem imperdiet adipiscing nec sed nunc. Donec vitae lacus quis orci fermentum rutrum. Pellentesque nunc lorem, faucibus a erat a, hendrerit mollis tortor. Duis ornare orci et mi mattis imperdiet molestie.</p>
    </div>
  </article>
  <article class="video">
    <div class="thumb t2" role="img" aria-label="Video still of a small child sitting on grass with puppies">
      <svg width="36" height="36" viewBox="0 0 36 36"><circle cx="18" cy="18" r="17" fill="rgba(0,0,0,.55)" stroke="#fff" stroke-width="2"/><path d="M14 11v14l11-7z" fill="#fff"/></svg>
    </div>
    <div class="copy">
      <h2>Lorem ipsum dolor sit amet</h2>
      <p>Aenean turpis lorem, volutpat ut facilisis in, tristique ac libero. Fusce eget ante lacinia, porttitor mauris nec, euismod mi. Nullam eros magna, laoreet vel mollis malesuada, scelerisque non elit. Etiam a augue sit amet massa commodo pulvinar eget, erat a accumsan fringilla. Nam ligula ipsum, pellentesque in dolor vel, finibus hendrerit nisl. Cras varius, massa malesuada mollis pulvinar, leo enim porta lorem, eu ultricies mauris diam eget nulla.</p>
    </div>
  </article>
  <article class="video">
    <div class="thumb t3" role="img" aria-label="Video still of a puppy chasing a football on a lawn">
      <svg width="36" height="36" viewBox="0 0 36 36"><circle cx="18" cy="18" r="17" fill="rgba(0,0,0,.55)" stroke="#fff" stroke-width="2"/><path d="M14 11v14l11-7z" fill="#fff"/></svg>
    </div>
    <div class="copy">
      <h2>Suspendisse faucibus est ornare</h2>
      <p>Duis at diam nunc. Aliquam vitae augue volutpat, ornare turpis condimentum, cursus dolor. Cras mattis faucibus urna quis convallis. Vestibulum laoreet at ipsum ac pretium venenatis. Nam ac velit iaculis, semper nunc sit amet, suscipit tortor. In rutrum lorem arcu, quis laoreet tellus commodo at amet. Curabitur pulvinar mauris diam at, et consectetur mi tempus eu.</p>
    </div>
  </article>
  <article class="video">
    <div class="thumb t4" role="img" aria-label="Video still of a dog eating from a bowl">
      <svg width="36" height="36" viewBox="0 0 36 36"><circle cx="18" cy="18" r="17" fill="rgba(0,0,0,.55)" stroke="#fff" stroke-width="2"/><path d="M14 11v14l11-7z" fill="#fff"/></svg>
    </div>
    <div class="copy">
      <h2>Proin nec tortor eget</h2>
      <p>There are many variations of passages of Lorem Ipsum available, but the majority have suffered alteration in some form, by injected humour, or randomised words which don't look even slightly believable. If you are going to use a passage of Lorem Ipsum, you need to be sure there isn't anything embarrassing hidden in the middle of text.</p>
    </div>
  </article>
</section>

<footer class="footer">
  <div class="cols">
    <div class="col c1"><h3>Quick Links</h3><ul><li>Why Raw</li><li>How to Use</li><li>Where to Buy</li><li>Success Stories</li><li>How to Use</li><li>Where to Buy</li><li>Contact Us</li></ul></div>
    <div class="col c2"><h3>Top Products</h3><ul><li>Product 1</li><li>Product 2</li><li>Product 3</li><li>Product 4</li><li>Product 5</li><li>Product 6</li><li>Product 7</li></ul></div>
    <div class="col c3"><h3>Where to Buy</h3><ul><li>Find a Retailer</li><li>Find a Local Distributor</li><li>Call to Order</li></ul></div>
    <div class="col c4"><h3>Contact Information</h3><ul>
      <li><svg width="7" height="9" viewBox="0 0 7 9"><path d="M3.5 0A3.2 3.2 0 0 0 .3 3.2C.3 5.5 3.5 9 3.5 9s3.2-3.5 3.2-5.8A3.2 3.2 0 0 0 3.5 0z" fill="#e8731a"/></svg>Copper Ridge Holdings, Inc.</li>
      <li style="padding-left:11px">2740 Copper Rd</li>
      <li style="padding-left:11px">Eagan, MN 55148</li>
      <li><svg width="8" height="8" viewBox="0 0 8 8"><path d="M1.5 0 3 2 2 3.2a5 5 0 0 0 2.8 2.8L6 5l2 1.5L7 8C3 8 0 5 0 1z" fill="#e8731a"/></svg>+1 (800) 555-0142</li>
    </ul></div>
    <div class="col c5"><h3>Newsletter</h3>
      <p>Subscribe for our monthly feeding tips and member offers.</p>
      <div class="field"></div>
      <span class="subscribe">Subscribe</span>
      <div class="social"><i></i><i></i><i></i><i></i><i></i></div>
    </div>
  </div>
  <div class="bottom">Meadow Paw © 2014. Privacy Policy</div>
</footer>

</body>
</html>
```